High Tech Real Estate Startup needs a business card

We are developing an innovative real estate marketing product based around advanced search and virtual reality.

We talk to people, we need business cards.

Target Market(s)

The target market is technology professionals and realtors.

Contact Information for Business Card

The information to be included will include

Name
Title
Phone Number
E-mail Address
www.zelquin.com

It should use simple iconography for each one of those fields.

Font styles to use
Other font styles liked:
• Co, Jubilat, Avenir

Colors

Designer to choose colors to be used in the design.

Requirements
Must have
• Clean aesthetic,
• Good use of negative space.
• It should use our company logo, shown in the attached file. It is able to use the negative of that logo (coloured font and white background) and I have attached other acceptable accent colours in a swatch file.
Should not have
• Should not be too busy
• No extraneous text (slogans, tag lines etc)

```html
<!DOCTYPE html>
<html lang="en">
<head>
<meta charset="utf-8">
<title>Zelquin Business Card</title>
<link href="https://fonts.googleapis.com/css2?family=Open+Sans:wght@400;600;700&display=swap" rel="stylesheet">
<style>
  :root {
    --backdrop: #2f2f31;
    --teal: #3fb1b2;
    --teal-deep: #2e9597;
    --paper: #f4f4f4;
    --ink: #2b2b2b;
    --rule: #9fd3d4;
  }
  * { margin: 0; padding: 0; box-sizing: border-box; }
  html, body {
    width: 799px; height: 1200px; overflow: hidden;
    background: var(--backdrop);
    font-family: "Open Sans", Arial, sans-serif;
  }
  .card {
    position: absolute; left: 90px;
    width: 620px; height: 354px;
    border-radius: 26px; overflow: hidden;
  }
  .card-front { top: 150px; background: var(--teal); }
  .card-back { top: 700px; background: var(--paper); }

  .front-name {
    position: absolute; inset: 0;
    display: flex; align-items: center; justify-content: center;
    font-size: 72px; font-weight: 600; letter-spacing: 3px;
    color: var(--teal-deep);
  }

  .band {
    position: absolute; left: 0; right: 0; top: 52px; height: 96px;
    background: var(--teal);
    display: flex; align-items: center; justify-content: center;
  }
  .band-name {
    font-size: 60px; font-weight: 600; letter-spacing: 3px; color: #ffffff;
  }
  .rule {
    position: absolute; left: 60px; right: 60px; height: 1px; background: var(--rule);
  }
  .rule-top { top: 166px; }
  .rule-bottom { top: 310px; }

  .person {
    position: absolute; top: 180px; left: 0; right: 0; text-align: center;
  }
  .person-name { font-size: 22px; font-weight: 700; color: var(--ink); }
  .person-title { font-size: 14px; font-weight: 600; color: var(--teal); margin-top: 2px; }

  .contacts {
    position: absolute; top: 260px; left: 0; right: 0;
    display: flex; justify-content: center; gap: 22px;
    font-size: 15px; color: var(--ink);
  }
  .contact { display: flex; align-items: center; gap: 7px; white-space: nowrap; }
  .contact-icon { width: 16px; height: 16px; flex: none; }
  .contact-web { font-weight: 600; }
</style>
</head>
<body>
  <section class="card card-front">
    <div class="front-name">ZELQUIN</div>
  </section>

  <section class="card card-back">
    <div class="band"><span class="band-name">ZELQUIN</span></div>
    <div class="rule rule-top"></div>
    <div class="person">
      <div class="person-name">Dana Reyes Holt</div>
      <div class="person-title">Managing Director</div>
    </div>
    <div class="contacts">
      <div class="contact">
        <svg class="contact-icon" viewBox="0 0 16 16" aria-hidden="true">
          <circle cx="8" cy="8" r="8" fill="var(--teal)"/>
          <path d="M5 4.5h2l.8 2-1 .8a5 5 0 0 0 2 2l.8-1 2 .8v2c-4 .5-7-2.5-6.6-6.6z" fill="#fff"/>
        </svg>
        <span>314.208.7761</span>
      </div>
      <div class="contact">
        <svg class="contact-icon" viewBox="0 0 16 16" aria-hidden="true">
          <circle cx="8" cy="8" r="8" fill="var(--teal)"/>
          <rect x="4" y="5.2" width="8" height="5.6" fill="#fff"/>
          <path d="M4 5.2l4 3 4-3" fill="none" stroke="var(--teal)" stroke-width="0.9"/>
        </svg>
        <span>dana@zelquin.com</span>
      </div>
      <div class="contact">
        <svg class="contact-icon" viewBox="0 0 16 16" aria-hidden="true">
          <circle cx="8" cy="8" r="8" fill="var(--teal)"/>
          <circle cx="8" cy="8" r="4" fill="none" stroke="#fff" stroke-width="1"/>
          <ellipse cx="8" cy="8" rx="1.7" ry="4" fill="none" stroke="#fff" stroke-width="0.9"/>
          <path d="M4 8h8" stroke="#fff" stroke-width="0.9"/>
        </svg>
        <span class="contact-web">www.zelquin.com</span>
      </div>
    </div>
    <div class="rule rule-bottom"></div>
  </section>
</body>
</html>
```